Heritage Hollow Business Cards

Require a business card design. <br/><br/>Needs to include logo (either round or long version) plus these details:<br/>Maya Torvell<br/>Heritage Hollow<br/>maya@kelvadtrading.com.au<br/>02 6481 7395<br/>PO Box Glenwarra NSW 2791<br/>www.heritagehollow.com.au<br/><br/>I need in an editable format so that I can create for multiple staff members. <br/><br/>

Target Market(s)

We are an online store selling renovation products to home owners are builders. Looking for a classic classy design.

Industry/Entity Type

Home And Garden

Contact Information for Business Card

Maya Torvell
Heritage Hollow
maya@kelvadtrading.com.au
02 6481 7395
PO Box Glenwarra NSW 2791
www.heritagehollow.com.au

Colors

Designer to choose colors to be used in the design.

Requirements
Must have
• Must include Logo.

```html
<!DOCTYPE html>
<html lang="en">
<head>
<meta charset="utf-8">
<title>Heritage Hollow Business Cards</title>
<link rel="stylesheet" href="https://fonts.googleapis.com/css2?family=Raleway:ital,wght@0,400;0,500;1,400&display=swap">
<style>
  :root {
    --page: #ffffff;
    --ink: #000000;
    --paper: #ffffff;
    --mark-grey: #575757;
    --mark-light: #e6e6e6;
    --card-edge: #8a8a8a;
  }
  * { margin: 0; padding: 0; box-sizing: border-box; }
  html, body {
    width: 1200px;
    height: 923px;
    overflow: hidden;
    background: var(--page);
    font-family: "Raleway", sans-serif;
  }
  .stage { position: relative; width: 1200px; height: 923px; }

  .card {
    position: absolute;
    width: 527px;
    height: 310px;
    overflow: hidden;
  }

  /* Back of card */
  .card-back {
    left: 429px;
    top: 174px;
    background: var(--ink);
  }
  .card-back .brand {
    position: absolute;
    left: 0;
    right: 0;
    top: 170px;
    text-align: center;
    color: var(--mark-light);
    font-size: 25px;
    font-weight: 500;
    line-height: 1.1;
  }

  /* Front of card */
  .card-front {
    left: 299px;
    top: 436px;
    background: var(--paper);
    border: 1px solid var(--card-edge);
  }
  .card-front .split {
    position: absolute;
    inset: 0;
    width: 100%;
    height: 100%;
  }
  .card-front .brand {
    position: absolute;
    left: 70px;
    top: 112px;
    color: var(--mark-grey);
    font-size: 25px;
    font-weight: 500;
    line-height: 1.1;
  }
  .holder {
    position: absolute;
    left: 345px;
    top: 60px;
    color: var(--paper);
  }
  .holder-name {
    font-size: 20px;
    font-weight: 400;
    letter-spacing: 0.5px;
    line-height: 1.2;
  }
  .holder-company {
    font-size: 14px;
    font-style: italic;
    line-height: 1.3;
  }
  .contact {
    position: absolute;
    right: 30px;
    bottom: 22px;
    list-style: none;
    text-align: right;
    color: var(--paper);
    font-size: 14.5px;
    line-height: 18.5px;
  }
</style>
</head>
<body>
<main class="stage">

  <section class="card card-back" aria-label="Business card back">
    <p class="brand">Heritage<br>Hollow</p>
  </section>

  <section class="card card-front" aria-label="Business card front">
    <svg class="split" viewBox="0 0 527 310" preserveAspectRatio="none" aria-hidden="true">
      <polygon points="370,0 527,0 527,310 112,310" fill="var(--ink)"/>
    </svg>

    <p class="brand">Heritage<br>Hollow</p>

    <div class="holder">
      <p class="holder-name">MAYA TORVELL</p>
      <p class="holder-company">Heritage Hollow</p>
    </div>

    <ul class="contact">
      <li>maya@kelvadtrading.com.au</li>
      <li>02 6481 7395</li>
      <li>PO Box Glenwarra NSW 2791</li>
      <li>www.heritagehollow.com.au</li>
    </ul>
  </section>

</main>
</body>
</html>
```